KVB Website

We need a website for a company based in Doha Qatar called Brightpath Talent Global. It is a global recruitment company, that specializes in both mass recruitment and headhunting. The company is the number 1 one stop shop for recruitment in Qatar. It recruits from all over the world Europe, Asia, Americas, Middle East, Africa for Qatar.

Target Market(s)

Multinational companies, fortune 500 company CEO's, any top earning companies that are looking for a large number of employees or headhunting employees.
Also for candidates looking for companies to work in Qatar.

Industry/Entity Type

Shop

Colors
ffffff

Requirements
Must have
• Most important qualities the website needs to have:
Clean
Modern
Elegant
Professional
Less Tabs
Minimalisitc

Some examples, I would like you to follow are here:
http://www.velmora.ca/
http://www.trovenkip.com/
https://quelbrandix.com/match#

The main color should be white and it has to have a very stylish, modern and cool look. While being minimalistic. I do not want too many tabs. I want it to be simplistic to understand. the only place where the pink logo color is should be in the logo. The logo color should not be anywhere else. It has to be absolutely sleek. Please follow the example websites that I have provided.

I will send the contact details you need to add later. There is no need for a log in page.

Whatever you think that may be important for a recruitment site do suggest. But there is no need for a log in area as we are a different kind of recruitment company.

There should be an area for testimonials from clients. There should also be an area for news flash for the latest countries we are hiring from and the latest companies we are hiring for and the latest positions we are looking for.

Show me the best please. Whoever gives me the best, I will give them an order for the 2nd website too.

Nice to have
• I have included a powerpoint to explain more!

```html
<!DOCTYPE html>
<html lang="en">
<head>
<meta charset="utf-8">
<title>Brightpath Talent Global – Contact</title>
<link rel="stylesheet" href="https://fonts.googleapis.com/css2?family=Zilla+Slab:ital,wght@0,300;0,400;0,600;0,700;1,400&display=swap">
<style>
  :root {
    --page-bg: #f6f6f6;
    --panel-bg: #efefef;
    --field-bg: #ffffff;
    --text-soft: #a3a3a3;
    --text-mid: #8c8c8c;
    --text-strong: #8a8a8a;
    --divider: #c9c9c9;
    --footer-bg: #ffffff;
    --footer-text: #6f6f6f;
  }
  * { box-sizing: border-box; margin: 0; padding: 0; }
  html, body { width: 1200px; height: 900px; overflow: hidden; }
  body {
    position: relative;
    background: var(--page-bg);
    font-family: "Zilla Slab", Georgia, serif;
    color: var(--text-soft);
  }

  /* message forms */
  .message-form {
    position: absolute;
    top: 0;
    width: 450px;
    height: 265px;
    background: var(--panel-bg);
  }
  .message-form--left { left: 113px; }
  .message-form--right { left: 620px; }
  .message-field {
    position: absolute;
    left: 171px;
    top: 0;
    width: 254px;
    height: 185px;
    background: var(--field-bg);
    border: none;
    outline: none;
    resize: none;
  }
  .send-button {
    position: absolute;
    right: 26px;
    top: 205px;
    width: 78px;
    height: 32px;
    background: var(--field-bg);
    border: none;
    font-family: "Zilla Slab", Georgia, serif;
    font-weight: 700;
    font-size: 21px;
    letter-spacing: 1px;
    color: var(--text-strong);
    line-height: 32px;
    text-align: center;
  }

  /* offices */
  .offices {
    position: absolute;
    left: 113px;
    top: 335px;
    width: 957px;
    height: 272px;
    background: var(--panel-bg);
  }
  .office-main {
    position: absolute;
    left: 26px;
    top: 22px;
  }
  .office-main__title {
    font-weight: 600;
    font-size: 26px;
    color: var(--text-strong);
    margin-bottom: 12px;
  }
  .office-main__details {
    list-style: none;
    padding-left: 35px;
    font-weight: 300;
    font-size: 22px;
    line-height: 29px;
    color: var(--text-soft);
  }
  .offices__divider {
    position: absolute;
    left: 354px;
    top: 36px;
    width: 1px;
    height: 208px;
    background: var(--divider);
  }
  .branch {
    position: absolute;
    width: 165px;
  }
  .branch__title {
    font-weight: 300;
    font-size: 23px;
    color: var(--text-mid);
    margin-bottom: 6px;
  }
  .branch__details {
    list-style: none;
    padding-left: 11px;
    font-weight: 400;
    font-size: 12.5px;
    line-height: 17px;
    color: var(--text-mid);
    white-space: nowrap;
  }

  /* footer */
  .site-footer {
    position: absolute;
    left: 0;
    bottom: 0;
    width: 1200px;
    height: 58px;
    background: var(--footer-bg);
    box-shadow: 0 -18px 30px rgba(0, 0, 0, 0.05);
    font-size: 13.5px;
    color: var(--footer-text);
  }
  .site-footer__copyright {
    position: absolute;
    left: 114px;
    top: 18px;
  }
  .site-footer__company {
    position: absolute;
    left: 221px;
    top: 18px;
    font-style: italic;
  }
</style>
</head>
<body>

  <form class="message-form message-form--left">
    <textarea class="message-field" aria-label="Message"></textarea>
    <button class="send-button" type="button">SEND</button>
  </form>

  <form class="message-form message-form--right">
    <textarea class="message-field" aria-label="Message"></textarea>
    <button class="send-button" type="button">SEND</button>
  </form>

  <section class="offices">
    <div class="office-main">
      <h2 class="office-main__title">Qatar/Main</h2>
      <ul class="office-main__details">
        <li>Adresse 1</li>
        <li>Adresse 2</li>
        <li>Phone: 312 840 576</li>
        <li>Phone2: 071 926 384</li>
        <li>Fax: 065 213 798</li>
        <li>E-mail: info@kvb.com</li>
      </ul>
    </div>

    <div class="offices__divider"></div>

    <div class="branch" style="left:425px; top:18px;">
      <h3 class="branch__title">Nepal</h3>
      <ul class="branch__details">
        <li>Adresse 1</li><li>Phone: 312 840 576</li><li>Fax: 312 840 577</li><li>E-mail: nepal@kvb.com</li>
      </ul>
    </div>
    <div class="branch" style="left:589px; top:19px;">
      <h3 class="branch__title">Philippines</h3>
      <ul class="branch__details">
        <li>Adresse 1</li><li>Phone: 312 840 576</li><li>Fax: 312 840 577</li><li>E-mail: nepal@kvb.com</li>
      </ul>
    </div>
    <div class="branch" style="left:768px; top:18px;">
      <h3 class="branch__title">Philippines</h3>
      <ul class="branch__details">
        <li>Adresse 1</li><li>Phone: 312 840 576</li><li>Fax: 312 840 577</li><li>E-mail: nepal@kvb.com</li>
      </ul>
    </div>
    <div class="branch" style="left:427px; top:135px;">
      <h3 class="branch__title">Philippines</h3>
      <ul class="branch__details">
        <li>Adresse 1</li><li>Phone: 312 840 576</li><li>Fax: 312 840 577</li><li>E-mail: nepal@kvb.com</li>
      </ul>
    </div>
    <div class="branch" style="left:591px; top:135px;">
      <h3 class="branch__title">Philippines</h3>
      <ul class="branch__details">
        <li>Adresse 1</li><li>Phone: 312 840 576</li><li>Fax: 312 840 577</li><li>E-mail: nepal@kvb.com</li>
      </ul>
    </div>
    <div class="branch" style="left:770px; top:134px;">
      <h3 class="branch__title">Philippines</h3>
      <ul class="branch__details">
        <li>Adresse 1</li><li>Phone: 312 840 576</li><li>Fax: 312 840 577</li><li>E-mail: nepal@kvb.com</li>
      </ul>
    </div>
  </section>

  <footer class="site-footer">
    <span class="site-footer__copyright">© Copyright</span>
    <span class="site-footer__company">Brightpath Talent Global 2014.</span>
  </footer>

</body>
</html>
```